Business Card Design

Buy and sell properties
Buy and rehab properties
Buy properties for cash
That is what I do but do need a logo
looking for some type of logo or design on it
Just started business
Back of card should say something like BUY HOUSES CASH
Overview: it is a new company. Basically I buy properties wholesale and fix them up and sell them or sell them to other fix and flippers
Background: company is new so not any background
Market: is basically anyone selling a house or buying a house. Someone that needs to sell house fast. Basically I am a cash home buyer!!!

Updates
Email on card should be:   harborlanerealtyinc@mailnest.com

Industry/Entity Type
House
Contact Information for Business Card
Harbor Lane Realty Inc
PO Box 718296
Coral Mill Key FL 33071

Dwight Kallum
dkallum@mailnest.com
305-271-5589

```html
<!DOCTYPE html>
<html lang="en">
<head>
<meta charset="utf-8">
<title>Harbor Lane Realty Inc — Business Card</title>
<link href="https://fonts.googleapis.com/css2?family=Questrial&family=Montserrat:wght@500;700&display=swap" rel="stylesheet">
<style>
  :root {
    --stage: #e6e8ea;
    --card: #ffffff;
    --ink: #3b3b3d;
    --ink-soft: #5a5a5c;
    --navy: #1b3f8f;
    --blue: #1d63ab;
    --green: #2f9a45;
    --green-light: #4fb85e;
    --rule: #8a8a8a;
  }
  * { box-sizing: border-box; margin: 0; padding: 0; }
  html, body { width: 1200px; height: 790px; overflow: hidden; }
  body {
    background: var(--stage);
    position: relative;
    font-family: "Questrial", sans-serif;
    color: var(--ink);
  }

  .card {
    position: absolute;
    background: var(--card);
    box-shadow: 0 2px 10px rgba(0,0,0,0.12);
    overflow: hidden;
  }

  /* Wordmark */
  .wordmark { display: flex; align-items: center; gap: 14px; }
  .wordmark__dot { border-radius: 50%; background: var(--blue); flex: none; }
  .wordmark__text { font-family: "Questrial", sans-serif; font-weight: 400; color: var(--ink); line-height: 1; }
  .wordmark__main { display: block; }
  .wordmark__sub { display: block; letter-spacing: 0.12em; margin-top: 6px; }

  /* Front card */
  .card--front { left: 70px; top: 40px; width: 580px; height: 320px; }
  .card--front .wordmark { position: absolute; left: 0; right: 0; top: 96px; justify-content: center; }
  .card--front .wordmark__dot { width: 46px; height: 46px; }
  .card--front .wordmark__main { font-size: 50px; }
  .card--front .wordmark__sub { font-size: 25px; }
  .tagline {
    position: absolute; left: 30px; right: 30px; top: 268px;
    display: flex; align-items: center; gap: 14px;
    font-family: "Montserrat", sans-serif; font-weight: 700;
    font-size: 15px; letter-spacing: 0.04em; color: var(--ink-soft);
    white-space: nowrap;
  }
  .tagline::before, .tagline::after { content: ""; height: 1px; background: var(--rule); flex: 1; }

  /* Back card */
  .card--back { left: 540px; top: 400px; width: 610px; height: 348px; }
  .card--back .wordmark { position: absolute; left: 40px; top: 58px; gap: 12px; }
  .card--back .wordmark__dot { width: 34px; height: 34px; }
  .card--back .wordmark__main { font-size: 36px; }
  .card--back .wordmark__sub { font-size: 19px; }
  .holder-rule {
    position: absolute; left: 30px; top: 172px; width: 430px; height: 1.5px; background: var(--navy);
  }
  .holder-name {
    position: absolute; left: 470px; top: 161px;
    font-family: "Montserrat", sans-serif; font-weight: 700; font-size: 17px; color: var(--ink);
  }
  .contact {
    position: absolute; left: 34px; top: 192px;
    font-family: "Montserrat", sans-serif; font-weight: 500; font-size: 15px; line-height: 22px; color: var(--ink);
    list-style: none;
  }
  .contact__line { display: flex; align-items: center; gap: 8px; }
  .contact__icon { width: 16px; height: 14px; flex: none; }
  .contact__company { font-weight: 700; margin-top: 2px; }
  .band-top { position: absolute; left: 0; right: 0; bottom: 46px; height: 4px; background: var(--navy); }
  .band {
    position: absolute; left: 0; right: 0; bottom: 0; height: 46px;
    background: linear-gradient(180deg, var(--green-light), var(--green));
  }

  /* Mark panel */
  .panel { position: absolute; left: 20px; top: 470px; width: 460px; height: 300px; background: var(--card); box-shadow: 0 2px 10px rgba(0,0,0,0.12); }
  .panel .wordmark { position: absolute; left: 0; right: 0; top: 108px; justify-content: center; }
  .panel .wordmark__dot { width: 44px; height: 44px; }
  .panel .wordmark__main { font-size: 46px; }
  .panel .wordmark__sub { font-size: 23px; }
</style>
</head>
<body>

  <section class="card card--front" aria-label="Card front">
    <div class="wordmark">
      <span class="wordmark__dot"></span>
      <span class="wordmark__text">
        <span class="wordmark__main">Harbor Lane</span>
        <span class="wordmark__sub">Realty Inc</span>
      </span>
    </div>
    <p class="tagline">BUY HOUSES CASH</p>
  </section>

  <section class="card card--back" aria-label="Card back">
    <div class="wordmark">
      <span class="wordmark__dot"></span>
      <span class="wordmark__text">
        <span class="wordmark__main">Harbor Lane</span>
        <span class="wordmark__sub">Realty Inc</span>
      </span>
    </div>
    <div class="holder-rule"></div>
    <p class="holder-name">Dwight Kallum</p>
    <ul class="contact">
      <li class="contact__line">
        <svg class="contact__icon" viewBox="0 0 16 14" aria-hidden="true"><path d="M1 5 Q8 -1 15 5 L13 7 L11 5 L5 5 L3 7 Z" fill="var(--navy)"/><rect x="3" y="7" width="10" height="6" rx="1" fill="var(--navy)"/></svg>
        305-271-5589
      </li>
      <li class="contact__line">
        <svg class="contact__icon" viewBox="0 0 16 14" aria-hidden="true"><rect x="1" y="2" width="14" height="10" fill="var(--navy)"/><path d="M1 2 L8 8 L15 2" stroke="#fff" stroke-width="1.2" fill="none"/></svg>
        dkallum@mailnest.com
      </li>
      <li class="contact__company">Harbor Lane Realty Inc</li>
      <li>PO Box 718296 Coral Mill Key FL</li>
    </ul>
    <div class="band-top"></div>
    <div class="band"></div>
  </section>

  <section class="panel" aria-label="Brand mark">
    <div class="wordmark">
      <span class="wordmark__dot"></span>
      <span class="wordmark__text">
        <span class="wordmark__main">Harbor Lane</span>
        <span class="wordmark__sub">Realty Inc</span>
      </span>
    </div>
  </section>

</body>
</html>
```